Redesign This Psychology Website

We would like a slight redesign of this successful psychology (relationship counselling) website:

www.TheKelvaleClinic.com.au

We are updating the website, and we'd like a slight refresh of the design and style.

Please keep to very similar colours, and use the same logo. We're looking for around 10 page templates, however the main one is the home page.

Keep in mind, this website already converts quite well, so we want a new, fresh design in keeping with this one. Please don't bother designing something too extremely different.

thanks :)

Target Market(s)

couples who are looking for relationship counselling. Men and women, 25 - 70, across Australia

Industry/Entity Type

Psychology

Number of Pages Required

5+ page

Font styles to use
Sans Serif

Colors
87cfc6
b7a5cd
ec1f27
ffffff
cee9f5

Requirements
Must have
• a similar look to the current design, just looking for a slight refresh.
• Search bar
• Areas for lots of photos
• same logo
• lots of content areas
Nice to have
• great content areas, where we can display a lot of content and our areas.
Should not have
• no colors like orange, etc.
• should not have a totally different feel.

```html
<!DOCTYPE html>
<html lang="en">
<head>
<meta charset="utf-8">
<title>The Kelvale Clinic – Relationship Counselling</title>
<link href="https://fonts.googleapis.com/css2?family=Roboto:wght@300;400;500;700&display=swap" rel="stylesheet">
<style>
:root{
  --teal:#167f8c;
  --teal-dark:#0f6772;
  --teal-deep:#0b5560;
  --red:#e5323a;
  --red-soft:#c9505a;
  --ink:#333;
  --muted:#555;
  --white:#fff;
}
*{box-sizing:border-box;margin:0;padding:0}
html,body{width:1200px;height:3830px;overflow:hidden}
body{font-family:'Roboto',Arial,sans-serif;color:var(--ink);background:var(--white);position:relative}
.abs{position:absolute}
a{color:inherit;text-decoration:none}

/* top bar */
.topbar{left:0;top:0;width:1200px;height:36px;background:var(--teal-dark);color:#fff;font-size:14px}
.topbar .phone{left:97px;top:9px;display:flex;align-items:center;gap:8px}
.topbar .links{right:97px;top:9px;font-weight:500}
.topbar .links span{margin:0 8px;opacity:.7}

/* header */
.header{left:0;top:36px;width:1200px;height:138px;background:#fff}
.brand{left:97px;top:30px;display:flex;align-items:center;gap:14px}
.brand .dot{width:52px;height:52px;border-radius:50%;background:var(--teal);flex:none}
.brand .name{font-size:34px;font-weight:500;color:var(--teal);line-height:1}
.brand .tag{font-size:15px;color:var(--teal);margin-top:6px}
.search{left:735px;top:35px;width:363px;height:36px;border:1px solid #ccc;border-radius:3px;display:flex;align-items:center;padding-left:10px;font-size:14px;color:#888}
.search .btn{position:absolute;right:4px;top:4px;width:28px;height:26px;background:var(--red);border-radius:3px}
.nav{left:536px;top:104px;width:564px;display:flex;justify-content:space-between;font-size:15px;font-weight:500;color:#333}
.nav .active{color:var(--red);border-bottom:2px solid var(--red);padding-bottom:8px}

/* hero */
.hero{left:0;top:174px;width:1200px;height:528px;overflow:hidden}
.hero .photo{position:absolute;inset:0;background:linear-gradient(100deg,#d9d3c8 0%,#ece6dc 35%,#cbb7a0 60%,#e7e2d8 100%)}
.hero .label{left:102px;top:107px;background:var(--red);color:#fff;font-size:40px;font-weight:400;padding:14px 20px;letter-spacing:1px}
.hero .lead{left:102px;top:210px;width:560px;color:#fff;font-size:17px;line-height:1.6;text-shadow:0 1px 3px rgba(0,0,0,.45)}
.btn-teal{background:var(--teal);color:#fff;font-size:15px;font-weight:500;display:inline-flex;align-items:center;justify-content:center;border:2px solid #fff}
.hero .more{left:102px;top:293px;width:120px;height:51px}
.hero .wave{position:absolute;left:0;bottom:0}

/* section titles */
.title{left:0;width:1200px;text-align:center;color:var(--red);font-weight:500}
.title:after{content:"";display:block;width:80px;height:2px;background:var(--red);margin:18px auto 0}
.title.big{font-size:36px}
.title.mid{font-size:28px}
.rule{left:97px;width:1006px;height:2px;background:var(--teal)}

.mission{left:125px;top:898px;width:950px;text-align:center;font-size:14px;line-height:1.85;color:var(--muted)}

/* services */
.service{width:300px;text-align:center}
.service .icon{width:160px;height:160px;border-radius:50%;border:3px solid #ddd;margin:0 auto;display:flex;align-items:center;justify-content:center;box-shadow:0 2px 6px rgba(0,0,0,.15)}
.service .icon .in{width:136px;height:136px;border-radius:50%;display:flex;align-items:center;justify-content:center}
.service h3{font-size:20px;font-weight:500;margin-top:40px}
.service p{font-size:14px;line-height:1.8;color:var(--muted);margin-top:14px}

/* specialise */
.special{left:0;top:1590px;width:1200px;height:534px;background:linear-gradient(90deg,#18808d 0%,#2a8f9b 55%,#1d7985 100%)}
.special .txt{left:97px;top:72px;width:620px;color:#fff}
.special h2{font-size:27px;font-weight:500;line-height:1.45}
.special p{font-size:14px;line-height:1.85;margin-top:20px;opacity:.95}
.special .more{margin-top:26px;width:120px;height:50px;background:transparent}
.finder{left:761px;top:64px;width:339px;height:404px;background:var(--teal-deep);border:3px solid #fff;border-radius:4px;overflow:hidden;color:#fff}
.finder .head{height:118px;background:var(--red-soft);text-align:center;font-size:21px;font-weight:500;line-height:1.5;padding-top:20px}
.finder .wave{position:absolute;left:0;top:88px}
.finder .row{position:absolute;left:30px;width:280px;display:flex;align-items:center;justify-content:space-between;font-size:15px}
.finder .lab{width:80px;text-align:center;line-height:1.3}
.finder .field{width:190px;height:38px;border:2px solid #fff;border-radius:4px;font-size:13px;padding:0 10px;display:flex;align-items:center;justify-content:space-between}
.finder .go{position:absolute;left:113px;top:342px;width:108px;height:38px;background:var(--red);border:2px solid #fff;border-radius:3px;display:flex;align-items:center;justify-content:center;font-size:15px;font-weight:500}

/* gallery */
.gal{top:2287px;width:230px;height:240px;overflow:hidden;box-shadow:0 8px 10px -6px rgba(0,0,0,.35)}
.gal .ph{position:absolute;inset:0}
.gal .corner{position:absolute;right:0;bottom:0}
.gal .cap{position:absolute;right:12px;bottom:18px;color:#fff;font-weight:500;font-size:16px;text-align:right;line-height:1.35}
.dots{left:548px;top:2598px;display:flex;gap:6px}
.dots i{width:14px;height:14px;border-radius:50%;background:#bbb}
.dots i:first-child{background:var(--red)}

/* blog */
.card{top:2800px;width:324px;text-align:center}
.card .ph{height:238px;border:4px solid var(--teal)}
.card.red .ph{border-color:var(--red-soft)}
.card h3{font-size:17px;font-weight:500;line-height:1.5;margin-top:30px;color:var(--teal);height:52px;padding:0 30px}
.card.red h3{color:var(--red)}
.card p{font-size:14px;line-height:1.75;color:#333;margin-top:22px;padding:0 6px;height:75px}
.card .read{display:inline-flex;margin-top:22px;width:104px;height:40px;background:var(--teal);color:#fff;font-size:13px;font-weight:700;align-items:center;justify-content:center}
.card.red .read{background:var(--red)}

/* footer */
.footer{left:0;top:3318px;width:1200px;height:435px;background:var(--teal)}
.footer .wave{position:absolute;left:0;top:0}
.fbrand{left:97px;top:234px;display:flex;align-items:center;gap:14px;color:#fff}
.fbrand .dot{width:52px;height:52px;border-radius:50%;background:#fff;flex:none}
.fbrand .name{font-size:34px;font-weight:500;line-height:1}
.fbrand .tag{font-size:16px;margin-top:6px}
.fhead{top:140px;color:#fff;font-size:16px;font-weight:700;letter-spacing:.5px}
.fhead:after{content:"";display:block;width:30px;height:2px;background:#fff;margin-top:8px}
.citem{left:564px;display:flex;gap:20px;color:#fff;font-size:14px;line-height:1.55}
.citem .ic{width:40px;height:40px;border:2px solid #fff;border-radius:50%;flex:none;display:flex;align-items:center;justify-content:center}
.citem b{font-weight:700}
.input{left:891px;width:210px;height:36px;border:2px solid #fff;border-radius:3px;color:#fff;font-size:12px;padding:0 8px;display:flex;align-items:center}
.signup{left:891px;top:334px;width:118px;height:38px;background:var(--red);border:2px solid #fff;border-radius:3px;color:#fff;font-size:13px;font-weight:700;display:flex;align-items:center;justify-content:center}
.bottom{left:0;top:3753px;width:1200px;height:77px;background:var(--teal-deep);color:#fff;font-size:14px}
.bottom .copy{left:97px;top:30px}
.socials{left:948px;top:18px;display:flex;gap:10px}
.socials i{width:40px;height:40px;border:2px solid #fff;border-radius:50%;display:block}
</style>
</head>
<body>

<div class="abs topbar">
  <div class="abs phone">
    <svg width="13" height="13" viewBox="0 0 24 24"><path fill="#fff" d="M6.6 10.8a15 15 0 0 0 6.6 6.6l2.2-2.2c.3-.3.7-.4 1-.2 1.1.4 2.3.6 3.6.6.6 0 1 .4 1 1V20c0 .6-.4 1-1 1A17 17 0 0 1 3 4c0-.6.4-1 1-1h3.5c.6 0 1 .4 1 1 0 1.3.2 2.5.6 3.6.1.3 0 .7-.2 1z"/></svg>
    1300 555 014
  </div>
  <div class="abs links">Join Our Associate Program<span>|</span>Marriage Counselling<span>|</span>Relationship Counselling</div>
</div>

<header class="abs header">
  <div class="abs brand">
    <div class="dot"></div>
    <div><div class="name">The Kelvale Clinic</div><div class="tag">helping you create loving relationships</div></div>
  </div>
  <div class="abs search">Search
    <div class="btn"><svg width="28" height="26" viewBox="0 0 28 26"><circle cx="13" cy="12" r="5" fill="none" stroke="#fff" stroke-width="2"/><path d="M17 16l4 4" stroke="#fff" stroke-width="2"/></svg></div>
  </div>
  <nav class="abs nav">
    <a class="active">HOME</a><a>ABOUT US</a><a>RESOURCES</a><a>BLOG</a><a>SHOP</a><a>CONTACT</a>
  </nav>
</header>

<section class="abs hero">
  <div class="photo" role="img" aria-label="Smiling couple sitting together on a sofa in a bright living room"></div>
  <div class="abs label">THE KELVALE CLINIC</div>
  <p class="abs lead">At the Kelvale Clinic, we are a group of PSYCHOLOGISTS, Australia wide who are passionate about relationships.</p>
  <a class="abs btn-teal more">Read More</a>
  <svg class="wave" width="1200" height="150" viewBox="0 0 1200 150">
    <path d="M0 60 C300 150 700 150 1200 20 L1200 150 L0 150Z" fill="var(--teal)"/>
    <path d="M0 80 C300 160 700 150 1200 55 L1200 150 L0 150Z" fill="#fff"/>
  </svg>
</section>

<h1 class="abs title big" style="top:780px">Welcome To The Kelvale Clinic</h1>
<p class="abs mission">Our mission is to be the most highly regarded relationship help service in Australia, by delivering a comprehensive range of the highest quality relationship and marriage counselling and advice, and books and products to educate and enhance client's relationships. To have every client who comes through our doors leave feeling listened to, understood, and educated on how to build a better relationship with their partner, while at the same time bringing out the best in themselves.</p>
<div class="abs rule" style="top:1044px"></div>

<h2 class="abs title mid" style="top:1096px">Our Services</h2>
<div class="abs service" style="left:103px;top:1204px">
  <div class="icon"><div class="in" style="background:var(--teal)">
    <svg width="70" height="60" viewBox="0 0 70 60" fill="#fff"><circle cx="18" cy="10" r="7"/><circle cx="52" cy="10" r="7"/><path d="M8 22h16v18H8zM46 22h16v18H46zM20 42h10v16h-4V46h-6zM40 42h10v4h-6v12h-4z"/><rect x="28" y="30" width="14" height="4"/></svg>
  </div></div>
  <h3 style="color:var(--teal)">Relationship Counselling</h3>
  <p>Communication, Recovering from an affair, Loss of intimacy &amp; love, Power battles, Feeling like friends, not lovers</p>
</div>
<div class="abs service" style="left:450px;top:1204px">
  <div class="icon"><div class="in" style="background:var(--red)">
    <svg width="64" height="60" viewBox="0 0 64 60"><path d="M6 6h52v36H26l-12 12V42H6z" fill="#fff"/><path d="M32 36c-8-6-13-10-13-15a6 6 0 0 1 13-2 6 6 0 0 1 13 2c0 5-5 9-13 15z" fill="var(--red)"/></svg>
  </div></div>
  <h3 style="color:var(--red)">Sex Therapy Counselling</h3>
  <p>Low libido, Erectile difficulties, Premature ejaculation, Differing libidos, Porn addiction, Keeping sex exciting</p>
</div>
<div class="abs service" style="left:797px;top:1204px">
  <div class="icon"><div class="in" style="background:var(--teal)">
    <svg width="64" height="64" viewBox="0 0 64 64" fill="#fff"><circle cx="32" cy="26" r="9"/><path d="M16 52c0-10 7-16 16-16s16 6 16 16z"/><path d="M32 4v8M14 10l5 6M50 10l-5 6M8 24h7M49 24h7" stroke="#fff" stroke-width="3"/></svg>
  </div></div>
  <h3 style="color:var(--teal)">Narcissism Counselling</h3>
  <p>Managing narcissistic, superior, entitled, arrogant and lack of empathy tendencies in you or your partner</p>
</div>

<section class="abs special" role="img" aria-label="Teal tinted backdrop of a couple in conversation">
  <div class="abs txt">
    <h2>We Specialise in Relationship &amp; Marriage Counselling</h2>
    <p>At the Kelvale Clinic, we are a group of PSYCHOLOGISTS, Australia wide who are passionate about relationships and helping you with yours. Our vision is to provide the most highly regarded and comprehensive marriage counselling and relationship counselling, and sex therapy in Australia, at reasonable and affordable rates.</p>
    <p>When we are experiencing relationship and marriage problems, there can be a lot of pain and confusion, and it can often be difficult to cope with the other areas of our lives when we are struggling with problems with our partner.</p>
    <a class="btn-teal more">Read More</a>
  </div>
  <div class="abs finder">
    <div class="head">Find Our Psychologist<br>Near You</div>
    <svg class="wave" width="339" height="50" viewBox="0 0 339 50"><path d="M0 30 C120 0 220 0 339 30 L339 50 L0 50Z" fill="var(--teal-deep)"/></svg>
    <div class="row" style="top:166px"><div class="lab">Type of Counselling</div><div class="field">Select<span>⇕</span></div></div>
    <div class="row" style="top:232px"><div class="lab">Location</div><div class="field"></div></div>
    <div class="row" style="top:284px"><div class="lab">(or)<br>Postcode</div><div class="field"></div></div>
    <div class="go">Search</div>
  </div>
</section>

<h2 class="abs title mid" style="top:2176px">Our Photo Gallery</h2>
<div class="abs gal" style="left:97px"><div class="ph" role="img" aria-label="Couple embracing indoors" style="background:linear-gradient(135deg,#c9a78d,#8a6a58)"></div>
  <svg class="corner" width="230" height="150" viewBox="0 0 230 150"><path d="M230 0V150H20Z" fill="var(--teal)" opacity=".9"/></svg><div class="cap">Why are we<br>together</div></div>
<div class="abs gal" style="left:355px"><div class="ph" role="img" aria-label="Couple sitting apart after a disagreement" style="background:linear-gradient(135deg,#e3ddd6,#9c8f86)"></div>
  <svg class="corner" width="230" height="150" viewBox="0 0 230 150"><path d="M230 0V150H20Z" fill="var(--red)" opacity=".9"/></svg><div class="cap">Relationship<br>Start</div></div>
<div class="abs gal" style="left:613px"><div class="ph" role="img" aria-label="Couple in a counselling session" style="background:linear-gradient(135deg,#b59a80,#6f5a4b)"></div>
  <svg class="corner" width="230" height="150" viewBox="0 0 230 150"><path d="M230 0V150H20Z" fill="var(--teal)" opacity=".9"/></svg><div class="cap">The Matter<br>Most</div></div>
<div class="abs gal" style="left:868px"><div class="ph" role="img" aria-label="Couple arm wrestling at a table" style="background:linear-gradient(135deg,#d9d2cc,#8c7d74)"></div>
  <svg class="corner" width="230" height="150" viewBox="0 0 230 150"><path d="M230 0V150H20Z" fill="var(--red)" opacity=".9"/></svg><div class="cap">Harbour<br>Hotel</div></div>
<div class="abs dots"><i></i><i></i><i></i><i></i><i></i></div>
<div class="abs rule" style="top:2663px"></div>

<h2 class="abs title mid" style="top:2704px">Our Blog Posts</h2>
<article class="abs card" style="left:97px">
  <div class="ph" role="img" aria-label="Couple talking on a sofa" style="background:linear-gradient(135deg,#e6e2dc,#a89a8e)"></div>
  <h3>Ending Your Relationship With Respect and Even a Little Kindness</h3>
  <p>Every couple starts their relationship with great love, and great hopes and dreams of a happy future together, so...</p>
  <a class="read">READ MORE</a>
</article>
<article class="abs card red" style="left:438px">
  <div class="ph" role="img" aria-label="Woman sitting on a bench in a garden" style="background:linear-gradient(135deg,#8fae6b,#4d6e3d)"></div>
  <h3>Is one of you an Intimacy Withholder?</h3>
  <p>Do you feel like strangers? or just flat mates? One of the most important aspects of a marriage. For the great majority of us in our love relationship.</p>
  <a class="read">READ MORE</a>
</article>
<article class="abs card" style="left:779px">
  <div class="ph" role="img" aria-label="Couple in a tense conversation" style="background:linear-gradient(135deg,#d6d0ca,#8d8279)"></div>
  <h3>Would You Know If You're In An Emotionally Abusive Relationship?</h3>
  <p>Name-calling, possessiveness, manipulation – this kind of psychological torture can be subtle, but the scars aren't. When Mara, 20,...</p>
  <a class="read">READ MORE</a>
</article>

<footer class="abs footer">
  <svg class="wave" width="1200" height="110" viewBox="0 0 1200 110">
    <path d="M0 0H1200V20C900 -10 600 20 0 95Z" fill="#fff"/>
    <path d="M0 95C500 20 900 -5 1200 20V34C900 10 500 35 0 110Z" fill="var(--red)"/>
    <path d="M0 0H1200V12C900 -10 600 10 0 80Z" fill="#fff"/>
  </svg>
  <div class="abs fbrand">
    <div class="dot"></div>
    <div><div class="name">The Kelvale Clinic</div><div class="tag">helping you create loving relationships</div></div>
  </div>
  <div class="abs fhead" style="left:564px">CONTACT US</div>
  <div class="abs citem" style="top:200px"><div class="ic"><svg width="14" height="18" viewBox="0 0 14 18"><path d="M7 0a7 7 0 0 0-7 7c0 5 7 11 7 11s7-6 7-11a7 7 0 0 0-7-7zm0 9.5A2.5 2.5 0 1 1 7 4.5a2.5 2.5 0 0 1 0 5z" fill="#fff"/></svg></div><div><b>ADDRESS,</b><br>48 Fenwick Lane, Ashgrove,<br>QLD</div></div>
  <div class="abs citem" style="top:284px"><div class="ic"><svg width="16" height="16" viewBox="0 0 24 24"><path fill="#fff" d="M6.6 10.8a15 15 0 0 0 6.6 6.6l2.2-2.2c.3-.3.7-.4 1-.2 1.1.4 2.3.6 3.6.6.6 0 1 .4 1 1V20c0 .6-.4 1-1 1A17 17 0 0 1 3 4c0-.6.4-1 1-1h3.5c.6 0 1 .4 1 1 0 1.3.2 2.5.6 3.6.1.3 0 .7-.2 1z"/></svg></div><div><b>PHONE:</b><br>1300 555 014</div></div>
  <div class="abs citem" style="top:356px"><div class="ic"><svg width="18" height="14" viewBox="0 0 18 14"><rect x="1" y="1" width="16" height="12" fill="none" stroke="#fff" stroke-width="2"/><path d="M1 1l8 7 8-7" fill="none" stroke="#fff" stroke-width="2"/></svg></div><div><b>Mail:</b><br>info@kelvaleclinic.com.au</div></div>
  <div class="abs fhead" style="left:891px">CONTACT FORM</div>
  <div class="abs input" style="top:194px">Name</div>
  <div class="abs input" style="top:240px">Phone</div>
  <div class="abs input" style="top:286px">Email</div>
  <div class="abs signup">SIGNUP NOW</div>
</footer>

<div class="abs bottom">
  <div class="abs copy">Copyright © 2017 The Kelvale Clinic. All Right Reserved</div>
  <div class="abs socials"><i></i><i></i><i></i><i></i></div>
</div>

</body>
</html>
```